Rollers & Glides.com

Vertical Business Card with focus on branding with our icon. Information on card will be logo, persons name, position, phone number, email address and website. Use the the name Marcus Pellow, position President, phone number 480.915.2267, email Marcus@rollersandglides-demo.com, website www.rollersandglides-demo.com.

```html
<!DOCTYPE html>
<html lang="en">
<head>
<meta charset="utf-8">
<title>Rollers &amp; Glides.com — Business Card</title>
<link rel="stylesheet" href="https://fonts.googleapis.com/css2?family=Roboto+Condensed:wght@500&family=Roboto:wght@400;700&display=swap">
<style>
  :root {
    --brand-blue: #335fab;
    --card-white: #ffffff;
    --ink: #333333;
    --rule: #8a8a8a;
    --backdrop: #b9b9b9;
  }
  * { box-sizing: border-box; margin: 0; padding: 0; }
  html, body { width: 1200px; height: 1200px; overflow: hidden; }
  body {
    position: relative;
    background: var(--backdrop);
    font-family: "Roboto", Arial, sans-serif;
  }
  .card {
    position: absolute;
    top: 307px;
    width: 362px;
    height: 586px;
    border-radius: 16px;
    overflow: hidden;
  }
  .card--back { left: 221px; background: var(--brand-blue); }
  .card--front { left: 618px; background: var(--card-white); }

  /* back side: rotated brand line */
  .back-brand {
    position: absolute;
    left: 181px;
    top: 390px;
    transform-origin: 0 0;
    transform: rotate(-90deg);
    display: flex;
    align-items: center;
    gap: 14px;
    white-space: nowrap;
    color: var(--card-white);
    font-family: "Roboto Condensed", "Arial Narrow", sans-serif;
    font-weight: 500;
    font-size: 34px;
    letter-spacing: 1px;
    margin-top: -20px;
  }
  .brand-dot {
    display: inline-block;
    width: 40px;
    height: 40px;
    border-radius: 50%;
    background: currentColor;
    flex: none;
  }

  /* front side */
  .front-mark {
    position: absolute;
    left: 50%;
    top: 118px;
    width: 78px;
    height: 78px;
    margin-left: -39px;
    border-radius: 50%;
    background: var(--brand-blue);
  }
  .front-name {
    position: absolute;
    left: 0; right: 0;
    top: 228px;
    text-align: center;
    color: var(--brand-blue);
    font-family: "Roboto Condensed", "Arial Narrow", sans-serif;
    font-weight: 500;
    font-size: 30px;
    letter-spacing: 1px;
  }
  .person {
    position: absolute;
    left: 0; right: 0;
    top: 386px;
    text-align: center;
  }
  .person__name {
    color: var(--brand-blue);
    font-weight: 700;
    font-size: 22px;
    line-height: 24px;
  }
  .person__role {
    color: var(--ink);
    font-size: 17px;
    line-height: 22px;
  }
  .icon-row {
    position: absolute;
    left: 0; right: 0;
    top: 450px;
    display: flex;
    justify-content: center;
    align-items: center;
    gap: 4px;
  }
  .icon-row__rule { width: 52px; height: 1px; background: var(--rule); margin: 0 3px; }
  .icon {
    width: 25px; height: 25px;
    border-radius: 3px;
    background: var(--brand-blue);
    display: flex; align-items: center; justify-content: center;
  }
  .contact {
    position: absolute;
    left: 0; right: 0;
    top: 485px;
    text-align: center;
    color: var(--ink);
    font-size: 16.5px;
    line-height: 21.5px;
  }
  .contact__highlight { color: var(--brand-blue); }
</style>
</head>
<body>

  <section class="card card--back" aria-label="Card back">
    <div class="back-brand">
      <span class="brand-dot"></span>
      <span>Rollers &amp; Glides.com</span>
    </div>
  </section>

  <section class="card card--front" aria-label="Card front">
    <div class="front-mark"></div>
    <div class="front-name">Rollers &amp; Glides.com</div>

    <div class="person">
      <div class="person__name">MARCUS PELLOW</div>
      <div class="person__role">President</div>
    </div>

    <div class="icon-row">
      <span class="icon-row__rule"></span>
      <span class="icon" aria-label="Phone">
        <svg width="15" height="15" viewBox="0 0 16 16"><path fill="#fff" d="M1 5c0-2 3-3 7-3s7 1 7 3v1h-3V5H4v1H1zM4 7h8l2 7H2z"/><g fill="#335fab"><rect x="5" y="9" width="1.5" height="1.5"/><rect x="7.3" y="9" width="1.5" height="1.5"/><rect x="9.6" y="9" width="1.5" height="1.5"/><rect x="5" y="11.4" width="1.5" height="1.5"/><rect x="7.3" y="11.4" width="1.5" height="1.5"/><rect x="9.6" y="11.4" width="1.5" height="1.5"/></g></svg>
      </span>
      <span class="icon" aria-label="Email">
        <svg width="16" height="12" viewBox="0 0 16 12"><rect x="0.75" y="0.75" width="14.5" height="10.5" fill="none" stroke="#fff" stroke-width="1.3"/><path d="M1 1l7 6 7-6M1 11l5-5M15 11l-5-5" fill="none" stroke="#fff" stroke-width="1.1"/></svg>
      </span>
      <span class="icon" aria-label="Website">
        <svg width="16" height="16" viewBox="0 0 16 16"><circle cx="8" cy="8" r="7" fill="#fff"/><path d="M4 4c2 0 3 1 2 3s-2 1-2 3M9 2c0 2 3 2 2 4s1 3 2 3M9 11c1 0 2 1 1 3" fill="none" stroke="#335fab" stroke-width="1.6"/></svg>
      </span>
      <span class="icon-row__rule"></span>
    </div>

    <div class="contact">
      <div>480.915.2267</div>
      <div>Marcus@rollersandglides-demo.com</div>
      <div>www.<span class="contact__highlight">rollersandglides-demo</span>.com</div>
    </div>
  </section>

</body>
</html>
```